I need a logo that demonstrates multiple of the same with one of a distinguishing feature. I would like something that can be recognisable in silhouette format. The business designs Management systems bespoke the to the company helping them pre-qualify for work.
Something that can demonstrate a distinction between a collective group non of which are the same in shape or size, with the largest of these not the distinguished object (or something to that effect).
This is a new business no logo or artwork exists.
Target Market(s)
Small to Medium Size enterprises in the city and rural areas. Looking to make the step up.
Industry/Entity Type
Manufacture
Contact Information for Business Card
room for, Name, Email, phone number
Font styles to use
Requirements
Must have
- would like the silhouette to be recognisable
Nice to have
- would like it to incorporate the name Keystone Advisory Frameworks.
- Would like the same logo to be on both business cards and on corporate shirts
Should not have
- anything that may exclude rural trade or manufacturing.
- I don't want to appear as corporate, just professional

```html
<!DOCTYPE html>
<html lang="en">
<head>
<meta charset="utf-8">
<title>Keystone Advisory Frameworks – Business Card</title>
<link rel="stylesheet" href="https://fonts.googleapis.com/css2?family=Open+Sans:wght@400;600;700&display=swap">
<style>
  :root {
    --brand-red: #ec1f27;
    --brand-orange: #f07522;
    --card-white: #ffffff;
    --backdrop: #e9e6e3;
    --shadow: rgba(0, 0, 0, 0.18);
  }
  * { box-sizing: border-box; margin: 0; padding: 0; }
  html, body {
    width: 1200px; height: 900px; overflow: hidden;
    background: var(--backdrop);
    font-family: "Open Sans", Arial, sans-serif;
  }
  .canvas { position: relative; width: 1200px; height: 900px; }

  .card {
    position: absolute;
    box-shadow: 0 6px 18px var(--shadow);
    overflow: hidden;
  }

  /* Front */
  .card-front {
    left: 78px; top: 34px; width: 588px; height: 364px;
    background: var(--card-white);
  }
  .card-front .bands { position: absolute; inset: 0; }
  .brand {
    position: absolute; display: flex; align-items: center;
  }
  .brand-mark {
    border-radius: 50%;
    flex: none;
  }
  .brand-name {
    font-weight: 400; line-height: 1; text-transform: uppercase;
  }
  .brand-name .line-main { display: block; letter-spacing: 0.5px; }
  .brand-name .line-sub { display: block; letter-spacing: 2px; margin-top: 6px; }

  .card-front .brand { left: 108px; top: 48px; }
  .card-front .brand-mark {
    width: 96px; height: 96px; border: 3px solid var(--brand-red);
    margin-right: 20px;
  }
  .card-front .brand-name { color: var(--brand-red); }
  .card-front .line-main { font-size: 36px; }
  .card-front .line-sub { font-size: 14px; }

  .holder {
    position: absolute; right: 316px; top: 251px;
    text-align: right; color: var(--card-white);
  }
  .holder-name { font-size: 19px; font-weight: 700; line-height: 1.2; }
  .holder-role { font-size: 15px; font-weight: 400; line-height: 1.3; }

  .contacts {
    position: absolute; left: 292px; top: 240px;
    list-style: none; color: var(--card-white);
    font-size: 15px; line-height: 21px;
  }
  .contacts li { display: flex; align-items: center; }
  .contacts svg { width: 12px; height: 12px; margin-right: 14px; fill: var(--card-white); }

  .address {
    position: absolute; left: 103px; top: 318px;
    color: var(--card-white); font-size: 15px;
  }

  /* Back */
  .card-back {
    left: 388px; top: 505px; width: 567px; height: 352px;
    background: var(--brand-red);
  }
  .card-back .brand { left: 94px; top: 127px; }
  .card-back .brand-mark {
    width: 98px; height: 98px; border: 3px solid var(--card-white);
    margin-right: 20px;
  }
  .card-back .brand-name { color: var(--card-white); }
  .card-back .line-main { font-size: 35px; }
  .card-back .line-sub { font-size: 14px; }
</style>
</head>
<body>
<main class="canvas">

  <section class="card card-front" aria-label="Business card front">
    <svg class="bands" width="588" height="364" viewBox="0 0 588 364" aria-hidden="true">
      <polygon points="0,192 394,192 378,214 0,214" fill="var(--brand-orange)"/>
      <polygon points="0,218 384,218 411,182 588,182 588,364 0,364" fill="var(--brand-red)"/>
    </svg>

    <div class="brand">
      <span class="brand-mark"></span>
      <p class="brand-name">
        <span class="line-main">Keystone</span>
        <span class="line-sub">Advisory Frameworks</span>
      </p>
    </div>

    <div class="holder">
      <p class="holder-name">Daniel Hartley</p>
      <p class="holder-role">Managing Director</p>
    </div>

    <ul class="contacts">
      <li>
        <svg viewBox="0 0 24 24"><path d="M6.6 10.8a15.1 15.1 0 0 0 6.6 6.6l2.2-2.2a1 1 0 0 1 1-.25 11.4 11.4 0 0 0 3.6.57 1 1 0 0 1 1 1V20a1 1 0 0 1-1 1A17 17 0 0 1 3 4a1 1 0 0 1 1-1h3.5a1 1 0 0 1 1 1c0 1.25.2 2.45.57 3.57a1 1 0 0 1-.25 1z"/></svg>
        044-987 654 321
      </li>
      <li>
        <svg viewBox="0 0 24 24"><path d="M2 5h20v14H2z M2 5l10 8 10-8" fill="var(--card-white)"/><path d="M3 6l9 7 9-7" stroke="var(--brand-red)" stroke-width="2" fill="none"/></svg>
        hello@keystoneaf.com
      </li>
      <li>
        <svg viewBox="0 0 24 24"><circle cx="12" cy="12" r="10"/><path d="M2 12h20M12 2c3 3 3 17 0 20M12 2c-3 3-3 17 0 20" stroke="var(--brand-red)" stroke-width="1.6" fill="none"/></svg>
        www.keystoneaf.com
      </li>
    </ul>

    <p class="address">48 Mill Lane, Harrow Green, Northshire, 204518.</p>
  </section>

  <section class="card card-back" aria-label="Business card back">
    <div class="brand">
      <span class="brand-mark"></span>
      <p class="brand-name">
        <span class="line-main">Keystone</span>
        <span class="line-sub">Advisory Frameworks</span>
      </p>
    </div>
  </section>

</main>
</body>
</html>
```